Landing Page & Email Signature

I am looking for a new landing page as well as an email signature to align with the change in business. I have included the new logo/emblem which I'd like incorporated into the design and the current landing page is www.delmorquivex.com.au should you wish to see the old version.

```html
<!DOCTYPE html>
<html lang="en">
<head>
<meta charset="utf-8">
<title>Delmor Transport</title>
<link href="https://fonts.googleapis.com/css2?family=Montserrat:wght@500;600;700;800&family=Lato:wght@400;700&display=swap" rel="stylesheet">
<style>
:root{
  --red:#a8001f;
  --red-dark:#8c0019;
  --ink:#161616;
  --text:#3a3a3a;
  --muted:#6b6b6b;
  --light:#eeeff1;
  --line:#dcdcdc;
  --white:#ffffff;
}
*{box-sizing:border-box;margin:0;padding:0}
html,body{width:1200px;height:3776px;overflow:hidden}
body{position:relative;background:var(--white);font-family:'Lato',sans-serif;color:var(--text)}
.btn{position:absolute;background:var(--red);color:var(--white);font-family:'Montserrat',sans-serif;font-weight:800;font-size:9px;letter-spacing:.3px;display:flex;align-items:center;justify-content:center;border-radius:2px;white-space:nowrap}
.btn-invert{background:var(--white);color:var(--red)}

/* header */
.site-header{position:absolute;left:0;top:0;width:1200px;height:110px;border-bottom:1px solid var(--line)}
.brand{position:absolute;left:136px;top:24px;display:flex;align-items:center;gap:10px}
.brand-dot{width:26px;height:26px;border-radius:50%;background:var(--red)}
.brand-name{font-family:'Montserrat',sans-serif;font-weight:800;color:var(--red);font-size:19px;line-height:21px}
.brand-url{font-family:'Montserrat',sans-serif;font-weight:800;color:var(--red);font-size:9px;margin-top:3px}
.follow{position:absolute;left:718px;top:27px;display:flex;align-items:center;gap:8px;font-family:'Montserrat',sans-serif;font-size:10px;font-weight:600;color:var(--ink)}
.social-dot{width:26px;height:26px;border-radius:50%}
.call{position:absolute;left:910px;top:20px;display:flex;align-items:center;gap:10px}
.call-icon{width:26px;height:26px;border-radius:50%;background:var(--red);display:flex;align-items:center;justify-content:center}
.call small{display:block;font-family:'Montserrat',sans-serif;font-weight:700;font-size:10px;color:var(--ink)}
.call strong{display:block;font-family:'Montserrat',sans-serif;font-weight:700;font-size:17px;color:var(--ink)}
.nav{position:absolute;top:70px;left:0;font-family:'Montserrat',sans-serif;font-size:14px;font-weight:600;color:var(--ink)}
.nav a{position:absolute;white-space:nowrap;color:var(--ink);text-decoration:none}
.nav a.active{color:var(--red);border-bottom:2px solid var(--red);padding-bottom:8px}

/* hero */
.hero{position:absolute;left:0;top:111px;width:1200px;height:581px;background:linear-gradient(90deg,#5a4e47 0%,#8f8983 35%,#b9b7b3 60%,#9e9c98 100%)}
.hero-title{position:absolute;left:646px;top:184px;color:var(--white);font-family:'Montserrat',sans-serif;font-weight:800;text-shadow:0 2px 4px rgba(0,0,0,.35);white-space:nowrap}
.hero-title .pre{font-size:31px;line-height:38px;display:block}
.hero-title .main{font-size:46px;line-height:56px;display:block;margin-top:4px}
.hero .btn{left:652px;top:314px;width:139px;height:50px;font-size:14px}
.dots{position:absolute;display:flex;gap:11px;align-items:center}
.dots span{width:6px;height:6px;border-radius:50%;background:var(--white)}
.dots span.on{width:9px;height:9px;background:var(--red);border:1px solid var(--white)}

/* section heading */
.section-title{position:absolute;left:0;width:1200px;text-align:center;font-family:'Montserrat',sans-serif;font-weight:700;font-size:24px;color:var(--ink)}
.section-rule{position:absolute;left:576px;width:48px;height:2px;background:var(--ink)}

/* services */
.service{position:absolute;top:816px;width:296px;height:333px;background:var(--white);box-shadow:0 2px 14px rgba(0,0,0,.09);text-align:center}
.service.featured{background:var(--red);color:var(--white)}
.service svg{position:absolute;left:98px;top:30px}
.service h3{position:absolute;top:125px;width:100%;font-family:'Montserrat',sans-serif;font-weight:500;font-size:16px;color:var(--ink)}
.service.featured h3,.service.featured p{color:var(--white)}
.service p{position:absolute;top:163px;left:43px;width:210px;font-size:12px;line-height:20px;color:var(--text)}
.service .btn{left:105px;top:264px;width:87px;height:32px}

/* about */
.about-band{position:absolute;left:0;top:1198px;width:1200px;height:437px;background:linear-gradient(180deg,#4d5a3a 0%,#7f8872 35%,#9aa1a8 60%,#c7cbd0 100%)}
.about-card{position:absolute;left:132px;top:1282px;width:385px;height:353px;background:var(--white);padding:32px 40px}
.about-card h2{font-family:'Montserrat',sans-serif;font-weight:800;font-size:24px;color:var(--ink)}
.about-card p{margin-top:36px;font-size:13px;line-height:21.7px;color:var(--text)}
.about-card .btn{left:40px;top:316px;width:87px;height:31px}

/* features */
.feature{position:absolute;top:1685px;display:flex;align-items:center;gap:12px;font-family:'Montserrat',sans-serif;font-weight:500;font-size:14px;color:var(--ink);white-space:nowrap}

/* gallery */
.gallery-band{position:absolute;left:0;top:1805px;width:1200px;height:535px;background:var(--light)}
.photo{position:absolute}
.gallery-band h2{position:absolute;left:674px;top:70px;font-family:'Montserrat',sans-serif;font-weight:800;font-size:25px;line-height:34px;color:var(--ink);width:400px}
.gallery-band p{position:absolute;left:674px;top:198px;width:396px;font-size:13px;line-height:21.7px;color:var(--text)}
.gallery-band .btn{left:674px;top:378px;width:88px;height:31px}
.dots.grey span{background:#b8b8b8;width:6px;height:6px}
.dots.grey span.on{background:var(--red);border:none}

/* blog */
.post{position:absolute;top:2464px;width:298px;height:412px;border:1px solid var(--line);background:var(--white)}
.post-photo{height:185px}
.post h3{position:absolute;top:218px;left:21px;width:260px;font-family:'Montserrat',sans-serif;font-weight:600;font-size:14px;line-height:20px;color:var(--ink)}
.post p{position:absolute;top:268px;left:21px;width:250px;font-size:11.5px;line-height:17.5px;color:var(--text)}
.post .btn{left:24px;top:350px;width:88px;height:33px}

/* contact */
.contact{position:absolute;left:0;top:2933px;width:1200px;height:520px;background:linear-gradient(180deg,#1b1c20 0%,#25272d 55%,#2b2a2a 100%)}
.contact h2{position:absolute;top:58px;width:100%;text-align:center;font-family:'Montserrat',sans-serif;font-weight:700;font-size:24px;color:var(--white)}
.contact .lead{position:absolute;top:98px;left:190px;width:820px;text-align:center;font-size:15px;line-height:24px;color:#e6e6e6}
.field{position:absolute;background:var(--white);font-size:12px;color:#333;padding:15px 14px}
.contact .btn{left:542px;top:437px;width:106px;height:41px;font-size:13px}

/* footer */
.footer{position:absolute;left:0;top:3453px;width:1200px;height:323px;background:var(--light)}
.footer .brand{left:132px;top:80px}
.footer .brand-name{font-size:30px;line-height:32px}
.footer .brand-url{font-size:14px;margin-top:6px}
.footer .brand-dot{width:40px;height:40px}
.foot-col{position:absolute;top:50px}
.foot-col h4{font-family:'Montserrat',sans-serif;font-weight:700;font-size:12px;color:var(--ink);margin-bottom:18px}
.foot-col li{list-style:none;font-family:'Montserrat',sans-serif;font-size:11px;color:var(--ink);line-height:19.6px}
.foot-item{display:flex;gap:14px;align-items:center;font-size:11.5px;line-height:15px;color:var(--ink);margin-bottom:20px}
.foot-ico{width:22px;height:22px;border-radius:50%;background:var(--white);display:flex;align-items:center;justify-content:center;flex:none}
.copyright{position:absolute;top:290px;width:100%;text-align:center;font-size:10px;color:var(--ink)}
</style>
</head>
<body>

<header class="site-header">
  <div class="brand">
    <span class="brand-dot"></span>
    <div>
      <div class="brand-name">DELMOR<br>TRANSPORT</div>
      <div class="brand-url">www.delmorquivex.com.au</div>
    </div>
  </div>
  <div class="follow">FOLLOW US
    <span class="social-dot" style="background:#3a5ba0"></span>
    <span class="social-dot" style="background:#1da1f2"></span>
    <span class="social-dot" style="background:#1f2a6b"></span>
  </div>
  <div class="call">
    <span class="call-icon"><svg width="13" height="13" viewBox="0 0 24 24"><path fill="#fff" d="M6.6 10.8a15 15 0 0 0 6.6 6.6l2.2-2.2c.3-.3.7-.4 1-.2 1.1.4 2.3.6 3.6.6.6 0 1 .4 1 1V20c0 .6-.4 1-1 1A17 17 0 0 1 3 4c0-.6.4-1 1-1h3.5c.6 0 1 .4 1 1 0 1.3.2 2.5.6 3.6.1.3 0 .7-.2 1z"/></svg></span>
    <div><small>CALL US</small><strong>+61455018372</strong></div>
  </div>
  <nav class="nav">
    <a class="active" style="left:586px">HOME</a>
    <a style="left:669px">ABOUT US</a>
    <a style="left:784px">SERVICES</a>
    <a style="left:892px">BLOG</a>
    <a style="left:975px">CONTACT US</a>
  </nav>
</header>

<section class="hero" role="img" aria-label="Courier in a red jacket with a yellow delivery backpack riding a scooter past a white building">
  <h1 class="hero-title"><span class="pre">WELCOME TO</span><span class="main">DELMOR TRANSPORT</span></h1>
  <span class="btn">READ MORE</span>
  <div class="dots" style="left:563px;top:545px"><span></span><span></span><span class="on"></span><span></span><span></span></div>
</section>

<h2 class="section-title" style="top:733px">OUR SERVICES</h2>
<div class="section-rule" style="top:778px"></div>

<article class="service" style="left:133px">
  <svg width="100" height="70" viewBox="0 0 100 70" fill="none" stroke="#a8001f" stroke-width="3">
    <circle cx="20" cy="48" r="14"/><circle cx="80" cy="48" r="14"/><circle cx="20" cy="48" r="5"/><circle cx="80" cy="48" r="5"/>
    <path d="M20 48 L40 30 H60 L72 18 M40 30 L50 48 H66 L80 48 M60 30 L66 48 M30 26 H46 M72 18 H82"/>
  </svg>
  <h3>Transportation</h3>
  <p>Lorem Ipsum is simply dummy text of the printing and types etting industry. Lorem Ipsum has been the industry's stan.</p>
  <span class="btn">READ MORE</span>
</article>
<article class="service featured" style="left:453px">
  <svg width="100" height="70" viewBox="0 0 100 70" fill="none" stroke="#fff" stroke-width="3">
    <rect x="38" y="4" width="24" height="20"/><rect x="26" y="24" width="24" height="20"/><rect x="50" y="24" width="24" height="20"/>
    <path d="M20 48 H80 M20 58 H80 M24 48 V62 M50 48 V62 M76 48 V62 M46 4 V12 H54 V4"/>
  </svg>
  <h3>Warehousing</h3>
  <p>Lorem Ipsum is simply dummy text of the printing and types etting industry. Lorem Ipsum has been the industry's stan.</p>
  <span class="btn btn-invert">READ MORE</span>
</article>
<article class="service" style="left:772px">
  <svg width="100" height="70" viewBox="0 0 100 70" fill="none" stroke="#a8001f" stroke-width="3">
    <path d="M20 10 H62 V52 H20 M62 24 H78 L92 38 V52 H62"/><circle cx="34" cy="56" r="7"/><circle cx="80" cy="56" r="7"/>
    <path d="M2 22 H16 M6 32 H16 M0 42 H16 M34 10 V24 H48 V10"/>
  </svg>
  <h3>Third-Party Logistics</h3>
  <p>Lorem Ipsum is simply dummy text of the printing and types etting industry. Lorem Ipsum has been the industry's stan.</p>
  <span class="btn">READ MORE</span>
</article>

<section class="about-band" role="img" aria-label="Motion-blurred motorcyclist riding a blue motorbike along a highway"></section>
<article class="about-card">
  <h2>ABOUT US</h2>
  <p>There are many variations of passages of Lorem Ipsum available, but the majority have suffered alteration in some form, by injected humour, or randomised words which don't look even slightly believable. If you are going to use a passage of Lorem Ipsum, you need to be sure there isn't anything embarrassing hidden in the middle of text. All the Lorem Ipsum generators on the Internet tend to repeat predefined .</p>
  <span class="btn">READ MORE</span>
</article>

<div class="feature" style="left:132px">
  <svg width="70" height="78" viewBox="0 0 70 78"><path d="M35 2 L67 20 V58 L35 76 L3 58 V20Z" fill="#111"/><path d="M22 42 V36 a13 13 0 0 1 26 0 V42 M22 40 h4 v10 h-4z M44 40 h4 v10 h-4z M46 50 q0 6 -9 6" fill="none" stroke="#fff" stroke-width="2.5"/></svg>
  24/7/365 SUPPORT
</div>
<div class="feature" style="left:369px">
  <svg width="70" height="78" viewBox="0 0 70 78"><path d="M35 2 L67 20 V58 L35 76 L3 58 V20Z" fill="#111"/><path d="M35 22 L49 28 V40 C49 48 42 54 35 56 C28 54 21 48 21 40 V28Z M28 39 L33 44 L42 34" fill="none" stroke="#fff" stroke-width="2.5"/></svg>
  100% SECURITY
</div>
<div class="feature" style="left:593px">
  <svg width="70" height="78" viewBox="0 0 70 78"><path d="M35 2 L67 20 V58 L35 76 L3 58 V20Z" fill="#111"/><path d="M22 26 H48 V54 H22Z M22 36 H48 M35 26 V36 M27 44 h7 v6 h-7z" fill="none" stroke="#fff" stroke-width="2.5"/></svg>
  WORLD CLASS PACKING
</div>
<div class="feature" style="left:876px">
  <svg width="70" height="78" viewBox="0 0 70 78"><path d="M35 2 L67 20 V58 L35 76 L3 58 V20Z" fill="#111"/><path d="M20 28 H40 V48 H20 M40 34 H47 L53 41 V48 H40 M12 34 H18 M14 40 H18" fill="none" stroke="#fff" stroke-width="2.5"/><circle cx="27" cy="50" r="3" fill="#fff"/><circle cx="47" cy="50" r="3" fill="#fff"/></svg>
  FAST DELIVERY
</div>

<section class="gallery-band">
  <div class="photo" role="img" aria-label="Green vintage scooter parked on paving" style="left:133px;top:44px;width:238px;height:202px;background:linear-gradient(160deg,#2f3a33,#3cb44a 55%,#6d6f6a)"></div>
  <div class="photo" role="img" aria-label="Red sports motorbike among plants" style="left:384px;top:44px;width:237px;height:202px;background:linear-gradient(160deg,#3a4a2c,#c8182a 50%,#6d6c6a)"></div>
  <div class="photo" role="img" aria-label="Black touring motorbike seen from the front" style="left:133px;top:262px;width:238px;height:202px;background:linear-gradient(160deg,#8a8a86,#1c1e26 55%,#7a7874)"></div>
  <div class="photo" role="img" aria-label="Close view of a dark blue motorbike dashboard" style="left:384px;top:262px;width:237px;height:202px;background:linear-gradient(160deg,#9a9994,#12183a 55%,#4c4f5a)"></div>
  <div class="dots grey" style="left:337px;top:486px"><span></span><span></span><span class="on"></span><span></span><span></span></div>
  <h2>Contrary to popular belief Lorem Ipsum is not simply random text.</h2>
  <p>There are many variations of passages of Lorem Ipsum available, but the majority have suffered alteration in some form, by injected humour, or randomised words which don't look even slightly believable. If you are going to use a passage of Lorem Ipsum, you need to be sure there isn't anything embarrassing hidden in the middle of text. All the Lorem Ipsum generators on the Internet tend to repeat predefined .</p>
  <span class="btn">READ MORE</span>
</section>

<h2 class="section-title" style="top:2385px">LATEST BLOG</h2>
<div class="section-rule" style="top:2430px"></div>

<article class="post" style="left:132px">
  <div class="post-photo" role="img" aria-label="Warehouse worker in a hi-vis vest checking shelves" style="background:linear-gradient(120deg,#3a2b22,#b99a7a 50%,#d96a2a 75%,#4a3a30)"></div>
  <h3>There are many variations of pass of Lorem Ipsum available.</h3>
  <p>Lorem Ipsum is simply dummy text of the printing and typesetting industry. Lorem Ipsum has been distribution of letters, as opposed to using Content here.</p>
  <span class="btn">READ MORE</span>
</article>
<article class="post" style="left:451px">
  <div class="post-photo" role="img" aria-label="Delivery rider on a motorbike with a red box" style="background:linear-gradient(180deg,#e4e4e4,#9a9a9a 60%,#4a4a4a)"></div>
  <h3>Contrary to popular belief Lorem Ipsum is not simply rando</h3>
  <p>Lorem Ipsum is simply dummy text of the printing and typesetting industry. Lorem Ipsum has been distribution of letters, as opposed to using Content here.</p>
  <span class="btn">READ MORE</span>
</article>
<article class="post" style="left:769px">
  <div class="post-photo" role="img" aria-label="Rows of parcels on automated sorting robots" style="background:linear-gradient(135deg,#1c2a52,#3a5a9a 50%,#c9a37a 80%,#1c2a52)"></div>
  <h3>Sed ut perspiciatis unde omnis iste natus error sit voluptat.</h3>
  <p>Lorem Ipsum is simply dummy text of the printing and typesetting industry. Lorem Ipsum has been distribution of letters, as opposed to using Content here.</p>
  <span class="btn">READ MORE</span>
</article>

<section class="contact" role="img" aria-label="Dim shipping container yard at dusk behind the contact form">
  <h2>CONTACT US</h2>
  <p class="lead">We can guarantee your satisfaction with our services. To prove, you may call our clients, who we have been serving for years to hear first-hand testimonies. We look forward to satisfy your current and future needs!</p>
  <div class="field" style="left:253px;top:179px;width:340px;height:44px">Your Name</div>
  <div class="field" style="left:606px;top:179px;width:341px;height:44px">Your Phone Number</div>
  <div class="field" style="left:253px;top:240px;width:340px;height:44px">Email Address</div>
  <div class="field" style="left:606px;top:240px;width:341px;height:44px">Subject</div>
  <div class="field" style="left:253px;top:302px;width:695px;height:105px">Message</div>
  <span class="btn">SUBMIT</span>
</section>

<footer class="footer">
  <div class="brand">
    <span class="brand-dot"></span>
    <div>
      <div class="brand-name">DELMOR<br>TRANSPORT</div>
      <div class="brand-url">www.delmorquivex.com.au</div>
    </div>
  </div>
  <div class="foot-col" style="left:482px">
    <h4>MENU</h4>
    <ul><li>HOME</li><li>ABOUT US</li><li>SERVICES</li><li>BLOG</li><li>CONTACT US</li></ul>
  </div>
  <div class="foot-col" style="left:655px">
    <h4>CONTACT US</h4>
    <div class="foot-item"><span class="foot-ico"><svg width="10" height="12" viewBox="0 0 10 12"><path d="M5 0a4 4 0 0 0-4 4c0 3 4 8 4 8s4-5 4-8a4 4 0 0 0-4-4z" fill="#333"/><circle cx="5" cy="4" r="1.4" fill="#fff"/></svg></span><span>2150 Larkmoor Avenue<br>Fenwick, CA 91820</span></div>
    <div class="foot-item"><span class="foot-ico"><svg width="10" height="10" viewBox="0 0 24 24"><path fill="#333" d="M6.6 10.8a15 15 0 0 0 6.6 6.6l2.2-2.2c.3-.3.7-.4 1-.2 1.1.4 2.3.6 3.6.6.6 0 1 .4 1 1V20c0 .6-.4 1-1 1A17 17 0 0 1 3 4c0-.6.4-1 1-1h3.5c.6 0 1 .4 1 1 0 1.3.2 2.5.6 3.6.1.3 0 .7-.2 1z"/></svg></span><span>Call Us<br>+61455018372</span></div>
    <div class="foot-item"><span class="foot-ico"><svg width="11" height="8" viewBox="0 0 11 8"><rect width="11" height="8" fill="#333"/><path d="M0 0 L5.5 4.5 L11 0" fill="none" stroke="#fff"/></svg></span><span>E mail Us<br>delmortransport@mailbox.com</span></div>
  </div>
  <div class="foot-col" style="left:962px">
    <h4>FOLLOW US</h4>
    <div class="foot-item"><span class="foot-ico"><span style="width:8px;height:8px;background:#333;border-radius:50%"></span></span><span>Like us on<br>FRIENDSPACE</span></div>
    <div class="foot-item"><span class="foot-ico"><span style="width:8px;height:8px;background:#333;border-radius:50%"></span></span><span>Follow us on<br>CHIRPLINE</span></div>
    <div class="foot-item"><span class="foot-ico"><span style="width:8px;height:8px;background:#333;border-radius:50%"></span></span><span>Follow us on<br>WORKLINK</span></div>
  </div>
  <p class="copyright">Copyright © 2022 All Rights Reserved</p>
</footer>

</body>
</html>
```